stationary for a modern hotel
Venmira Hotels
Project: stationary for a modern hotel
stationary for a modern hotel - Hospitality Industry
Creative Brief
Use same font as used in my logo
anything that can go very well with my logo
Simple
Ibrahimu Sadiqwale
G.M
Venmira Hotels Plot 318,Adekunle-Bassey Road,Tarmo District Abuja Nigeria
ibrah@venmirahotels.example
www.venmirahotels.example

```html
<!DOCTYPE html>
<html lang="en">
<head>
<meta charset="utf-8">
<title>Venmira Hotels – Business Card</title>
<link rel="stylesheet" href="https://fonts.googleapis.com/css2?family=Questrial&display=swap">
<style>
  :root {
    --backdrop: #e9e6e1;
    --card: #ffffff;
    --brand-gold: #a9804f;
    --name-brown: #5a3d22;
    --body-grey: #5b5b5b;
    --accent-red: #8a1a1c;
    --band-text: #ffffff;
  }
  html, body {
    margin: 0;
    padding: 0;
    width: 1200px;
    height: 778px;
    overflow: hidden;
    background: var(--backdrop);
  }
  .business-card {
    position: absolute;
    left: 50px;
    top: 73px;
    width: 1100px;
    height: 632px;
    background: var(--card);
    font-family: "Questrial", "Century Gothic", sans-serif;
    text-align: center;
    color: var(--body-grey);
  }
  .brand-wordmark {
    position: absolute;
    top: 105px;
    left: 0;
    right: 0;
    margin: 0;
    font-size: 50px;
    font-weight: 400;
    letter-spacing: 3px;
    color: var(--brand-gold);
  }
  .holder-name {
    position: absolute;
    top: 300px;
    left: 0;
    right: 0;
    margin: 0;
    font-size: 36px;
    font-weight: 400;
    color: var(--name-brown);
  }
  .holder-title {
    position: absolute;
    top: 348px;
    left: 0;
    right: 0;
    margin: 0;
    font-size: 36px;
    color: var(--brand-gold);
  }
  .company-name {
    position: absolute;
    top: 434px;
    left: 0;
    right: 0;
    margin: 0;
    font-size: 27px;
    color: var(--name-brown);
  }
  .company-address {
    position: absolute;
    top: 472px;
    left: 0;
    right: 0;
    margin: 0;
    font-size: 24px;
  }
  .contact-row {
    position: absolute;
    top: 508px;
    left: 0;
    right: 0;
    display: flex;
    justify-content: center;
    gap: 34px;
    font-size: 24px;
  }
  .contact-item {
    display: inline-flex;
    align-items: center;
    gap: 8px;
  }
  .contact-icon {
    width: 20px;
    height: 20px;
    fill: none;
    stroke: var(--body-grey);
    stroke-width: 1.8;
  }
  .rule-line {
    position: absolute;
    top: 562px;
    left: 0;
    right: 0;
    height: 3px;
    background: var(--accent-red);
  }
  .web-band {
    position: absolute;
    top: 578px;
    left: 0;
    right: 0;
    height: 54px;
    background: var(--accent-red);
    color: var(--band-text);
    font-size: 26px;
    letter-spacing: 3px;
    line-height: 54px;
  }
</style>
</head>
<body>
  <main class="business-card">
    <h1 class="brand-wordmark">VENMIRA HOTELS</h1>

    <h2 class="holder-name">Ibrahimu Sadiqwale</h2>
    <p class="holder-title">G.M</p>

    <p class="company-name">Venmira Hotels</p>
    <p class="company-address">Plot 318, Adekunle-Bassey Road, Tarmo District, Abuja, Nigeria</p>

    <div class="contact-row">
      <span class="contact-item">
        <svg class="contact-icon" viewBox="0 0 20 20" aria-hidden="true">
          <path d="M4 2 L7 2 L8.5 6 L6.5 7.5 C7.5 10 10 12.5 12.5 13.5 L14 11.5 L18 13 L18 16 C18 17 17 18 16 18 C8.5 17.5 2.5 11.5 2 4 C2 3 3 2 4 2 Z"/>
        </svg>
        +2348090417326
      </span>
      <span class="contact-item">
        <svg class="contact-icon" viewBox="0 0 20 20" aria-hidden="true">
          <rect x="5.5" y="1.5" width="9" height="17" rx="1.5"/>
          <line x1="8.5" y1="15.5" x2="11.5" y2="15.5"/>
        </svg>
        +2348090417326
      </span>
      <span class="contact-item">
        <svg class="contact-icon" viewBox="0 0 20 20" aria-hidden="true">
          <rect x="1.5" y="4" width="17" height="12"/>
          <polyline points="1.5,4 10,11 18.5,4"/>
        </svg>
        ibrah@venmirahotels.example
      </span>
    </div>

    <div class="rule-line"></div>
    <div class="web-band">www.venmirahotels.example</div>
  </main>
</body>
</html>
```